A new presentation to our clients

we are a Real Estate agency, our website is www.lumibrasa.com and it’s time to have a new, fashion and remarcable Business Card. we want to differentiate ourselves from other companies so we want a business card that differentiates us. we want the business card to impact our customers. in the competitive market that we have today, we have to be different and it is this difference that we seek

Target Market(s)

Real Estate Clients

Contact Information for Business Card

We search a totaly diferent card from the usual

Font styles to use
Sans Serif

Colors
e34197

Requirements
Must have
• Logo, adress, phone contact, e-mail, photo, and our website
Nice to have
• We would like to see a modern business card
Should not have
• Houses or building draws

```html
<!DOCTYPE html>
<html lang="en">
<head>
<meta charset="utf-8">
<title>Lumi Brasa — Business Card</title>
<link rel="stylesheet" href="https://fonts.googleapis.com/css2?family=Oswald:wght@600&family=Work+Sans:wght@400;500&display=swap">
<style>
  :root {
    --backdrop: #1b1b1c;
    --card: #131313;
    --card-edge: #1f1f1f;
    --name: #9a9a9a;
    --name-shadow: #050505;
    --foil: #dcdcdc;
    --brand: #e34197;
  }
  * { margin: 0; padding: 0; box-sizing: border-box; }
  html, body {
    width: 1200px; height: 900px; overflow: hidden;
    background: var(--backdrop);
  }
  .stage {
    position: relative; width: 1200px; height: 900px;
    display: flex; flex-direction: column; align-items: center; justify-content: center; gap: 26px;
  }
  .card {
    position: relative; width: 620px; height: 354px;
    background: linear-gradient(160deg, #181818 0%, var(--card) 60%, #101010 100%);
    border: 1px solid var(--card-edge);
    box-shadow: 0 18px 40px rgba(0,0,0,0.55);
  }
  /* front */
  .brand-name {
    position: absolute; left: 0; right: 0; top: 140px;
    text-align: center;
    font-family: "Work Sans", sans-serif; font-weight: 500;
    font-size: 58px; letter-spacing: 1px;
    color: var(--foil);
  }
  .brand-rule {
    position: absolute; left: 280px; top: 232px; width: 60px; height: 3px;
    background: var(--brand);
  }
  /* back */
  .portrait {
    position: absolute; left: 40px; top: 116px; width: 92px; height: 92px;
    border-radius: 50%;
    background: radial-gradient(circle at 40% 35%, #4a4a4a 0%, #2a2a2a 70%);
    border: 2px solid var(--brand);
  }
  .person {
    position: absolute; left: 140px; top: 136px; width: 144px; text-align: right;
  }
  .person-name {
    font-family: "Oswald", sans-serif; font-weight: 600;
    font-size: 26px; line-height: 32px; letter-spacing: 0.5px; text-transform: uppercase;
    color: var(--name);
    text-shadow: 0 1px 0 var(--name-shadow);
  }
  .person-role {
    font-family: "Work Sans", sans-serif; font-size: 15px;
    color: var(--brand);
  }
  .divider {
    position: absolute; left: 300px; top: 118px; width: 1px; height: 92px;
    background: var(--brand);
  }
  .contact-list {
    position: absolute; left: 322px; top: 118px; list-style: none;
    font-family: "Work Sans", sans-serif; font-size: 17px; color: var(--foil);
  }
  .contact-list li { display: flex; align-items: center; gap: 10px; height: 23px; }
  .contact-list svg { width: 11px; height: 11px; fill: none; stroke: var(--brand); stroke-width: 1.6; flex: none; }
  .address {
    position: absolute; left: 0; right: 0; bottom: 52px; text-align: center;
    font-family: "Work Sans", sans-serif; font-size: 17px; letter-spacing: 0.3px;
    color: var(--foil);
  }
</style>
</head>
<body>
<main class="stage">
  <section class="card card-front">
    <div class="brand-name">Lumi Brasa</div>
    <div class="brand-rule"></div>
  </section>

  <section class="card card-back">
    <div class="portrait" role="img" aria-label="Portrait photo of the director"></div>
    <div class="person">
      <div class="person-name">Daniel Reyes</div>
      <div class="person-role">Director</div>
    </div>
    <div class="divider"></div>
    <ul class="contact-list">
      <li>
        <svg viewBox="0 0 12 12"><path d="M2 1.5h2l1 2.5-1.2 1a6 6 0 0 0 3.2 3.2l1-1.2 2.5 1v2c-4.5.3-8.8-4-8.5-8.5z"/></svg>
        (+351) 210 448 352
      </li>
      <li>
        <svg viewBox="0 0 12 12"><rect x="1" y="4.5" width="10" height="4.5"/><rect x="3" y="1" width="6" height="3.5"/><rect x="3" y="8" width="6" height="3"/></svg>
        (+351) 210 448 359
      </li>
      <li>
        <svg viewBox="0 0 12 12"><rect x="1" y="2.5" width="10" height="7"/><path d="M1 2.5l5 4 5-4"/></svg>
        geral@lumibrasa.com
      </li>
      <li>
        <svg viewBox="0 0 12 12"><circle cx="6" cy="6" r="5"/><path d="M1 6h10M6 1c2.5 2.8 2.5 7.2 0 10M6 1c-2.5 2.8-2.5 7.2 0 10"/></svg>
        www.lumibrasa.com
      </li>
    </ul>
    <div class="address">Rua das Camélias, 57 4400-210, Vila Nova de Gaia</div>
  </section>
</main>
</body>
</html>
```